I want to redesign the Tallvex corporate website

Morrowdale Farms Limited (Tallvex) is a Nigerian integrated agribusiness and premium food company operating across agriculture, food processing and nationwide FMCG distribution.
We are redesigning our corporate website to reflect our evolution into a modern, premium food company capable of serving institutional buyers, distributors, retailers, investors and consumers. The new website should feel comparable to the websites of leading global food brands — not a typical agricultural website.

Target Market(s)

Nigeria / Africa

Industry/Entity Type

FMCG

Coding

Coded - Design and coding required

Number of Pages Required

5+ page

Colors

Designer to choose colors to be used in the design.

Requirements
Must have
• The website must communicate the following attributes consistently across every page, in both design and language. Premium Quality of finish signals quality of product , Clean Uncluttered layouts, disciplined use of elements ,Modern Current design language, not dated conventions ,Innovative and Forward-looking, technology-enabled , Sustainable Responsible practice made visible Nigerian with global standards, Proudly local in origin, international in execution
Nice to have
• Lots of white space , Fast loading, Premium photography,Mobile-first,Elegant typography,Minimal clutter, Rounded elements,High-end corporate feel, Smooth curved section transitions, Soft shadows
Should not have
• The new website should feel comparable to the websites of leading global food brands — not a typical agricultural website. Also do not copy the business profile as website , its is just a guide !

```html
<!DOCTYPE html>
<html lang="en">
<head>
<meta charset="utf-8">
<title>Tallvex — Integrated Agriculture. Nourishing Lives.</title>
<link href="https://fonts.googleapis.com/css2?family=Poppins:wght@400;500;600;700;800&family=Source+Serif+4:wght@400;500&display=swap" rel="stylesheet">
<style>
:root{
  --green:#0f4d2a;
  --green-deep:#0b3a1f;
  --green-footer:#08301a;
  --lime:#8cc63f;
  --lime-dark:#6fa92b;
  --orange:#e8601c;
  --mist:#dde5e0;
  --ink:#1d2a22;
  --muted:#4f5a53;
  --white:#ffffff;
}
*{box-sizing:border-box;margin:0;padding:0}
html,body{width:1200px;height:5042px;overflow:hidden}
body{position:relative;background:var(--white);font-family:"Source Serif 4",Georgia,serif;color:var(--ink)}
.abs{position:absolute}
.head{font-family:"Poppins",Arial,sans-serif}
.eyebrow{font-family:"Poppins",Arial,sans-serif;font-weight:600;font-size:10px;letter-spacing:.6px;color:var(--lime-dark);text-transform:uppercase}
.btn{position:absolute;display:flex;align-items:center;justify-content:center;gap:6px;border-radius:20px;font-family:"Source Serif 4",Georgia,serif;font-size:12.5px;color:#fff;height:32px;box-shadow:0 4px 10px rgba(0,0,0,.12)}
.btn-orange{background:var(--orange)}
.btn-green{background:var(--green)}
.arrow{display:inline-block;width:14px;height:10px}
.photo{position:absolute;overflow:hidden}

/* header */
.topbar{position:absolute;left:0;top:0;width:1200px;height:90px;border-bottom:1px solid #e6ebe7}
.phone-ico{position:absolute;left:252px;top:10px;width:36px;height:36px;border-radius:50%;background:var(--green);display:flex;align-items:center;justify-content:center}
.phone-txt{position:absolute;left:296px;top:14px;font-family:"Poppins",Arial,sans-serif;font-size:11px;line-height:14px;color:var(--ink)}
.phone-txt b{font-weight:600}
.logo{position:absolute;font-family:"Poppins",Arial,sans-serif;font-weight:700;color:var(--green)}
.nav{position:absolute;top:66px;left:0;width:1200px;font-size:12px;color:var(--ink)}
.nav span{position:absolute}
.nav .active::after{content:"";position:absolute;left:-8px;right:-8px;top:22px;height:2px;background:var(--green)}

/* hero */
.hero-title{position:absolute;left:150px;width:420px;top:178px;text-align:center;font-family:"Poppins",Arial,sans-serif;font-weight:700;font-size:47px;line-height:49px;color:var(--green)}
.hero-copy{position:absolute;left:198px;width:326px;top:336px;text-align:center;font-size:12px;line-height:18px;color:var(--muted)}

/* feature cards */
.fcard{position:absolute;top:656px;width:216px;height:190px;background:#fff;border-radius:18px;box-shadow:0 8px 24px rgba(15,77,42,.12);text-align:center}
.fcard .ico{position:absolute;left:76px;top:20px;width:64px;height:64px;border-radius:50%;display:flex;align-items:center;justify-content:center}
.fcard h3{position:absolute;top:92px;left:0;right:0;font-family:"Poppins",Arial,sans-serif;font-weight:600;font-size:12px;line-height:16px;color:var(--green)}
.fcard p{position:absolute;left:20px;right:20px;font-size:12.5px;line-height:17px;color:var(--muted)}

/* about */
.about-title{position:absolute;left:644px;top:940px;font-family:"Poppins",Arial,sans-serif;font-weight:700;font-size:44px;line-height:42px;color:var(--green)}
.about-copy{position:absolute;left:644px;width:330px;font-size:12.5px;line-height:20px;color:var(--muted)}

/* products */
.pcard{position:absolute;top:1605px;width:218px;height:286px;background:#fff;border-radius:18px;box-shadow:0 8px 22px rgba(15,77,42,.1)}
.pcard .pimg{position:absolute;left:18px;right:18px;top:18px;height:150px;border-radius:14px}
.pcard h3{position:absolute;left:26px;top:187px;font-family:"Poppins",Arial,sans-serif;font-weight:600;font-size:16px;color:var(--ink)}
.pcard p{position:absolute;left:26px;top:214px;width:140px;font-size:12.5px;line-height:17px;color:var(--muted)}
.pcard .go{position:absolute;right:14px;bottom:14px;width:36px;height:36px;border-radius:50%;border:1.5px solid var(--green);display:flex;align-items:center;justify-content:center}

/* value chain */
.vc-title{position:absolute;left:0;width:1200px;top:2152px;text-align:center;font-family:"Poppins",Arial,sans-serif;font-weight:700;font-size:43px;line-height:46px;color:var(--green)}
.step{position:absolute;width:210px}
.step h4{font-family:"Poppins",Arial,sans-serif;font-weight:600;font-size:15.5px;color:var(--ink);margin-bottom:2px}
.step p{font-size:12.5px;line-height:17px;color:var(--muted)}
.step.r{text-align:right}
.node{position:absolute;width:50px;height:50px;border-radius:50%;border:2px solid #d9e2dc;background:#fff;display:flex;align-items:center;justify-content:center}
.node i{width:38px;height:38px;border-radius:50%;background:var(--green);display:flex;align-items:center;justify-content:center}
.node.o i{background:var(--orange)}

/* sustainability */
.sus-title{position:absolute;left:158px;width:400px;top:3072px;text-align:center;font-family:"Poppins",Arial,sans-serif;font-weight:700;font-size:40px;line-height:41px;color:#fff}

/* quality */
.q-title{position:absolute;left:0;width:1200px;top:3530px;text-align:center;font-family:"Poppins",Arial,sans-serif;font-weight:700;font-size:42px;line-height:46px;color:var(--green)}
.qitem{position:absolute;width:210px}
.qitem h4{font-family:"Poppins",Arial,sans-serif;font-weight:600;font-size:16px;line-height:19px;color:var(--ink)}
.qitem p{font-size:12.5px;line-height:16px;color:var(--muted)}
.qicon{position:absolute;width:66px;height:66px;border-radius:50%;background:var(--orange);border:4px solid #fde3d6;display:flex;align-items:center;justify-content:center}

/* news */
.news{position:absolute;left:0;top:4062px;width:1200px;height:710px;background:var(--green);overflow:hidden}
.ncard{position:absolute;top:202px;width:294px;height:376px;background:var(--green);border-radius:22px;overflow:hidden}
.ncard .nimg{position:absolute;left:0;top:0;width:294px;height:220px;border-radius:22px}
.ncard .tag{position:absolute;left:0;right:0;top:236px;text-align:center;font-family:"Poppins",Arial,sans-serif;font-weight:600;font-size:10px;color:var(--lime)}
.ncard h3{position:absolute;left:14px;right:14px;top:256px;text-align:center;font-family:"Poppins",Arial,sans-serif;font-weight:600;font-size:16px;line-height:21px;color:#fff}
.ncard .date{position:absolute;left:0;right:0;top:336px;text-align:center;font-size:12.5px;color:#e3ece6}

/* footer */
.footer{position:absolute;left:0;top:4772px;width:1200px;height:270px;background:var(--green-footer)}
.f-h{position:absolute;font-family:"Poppins",Arial,sans-serif;font-weight:600;font-size:16px;color:var(--lime)}
.f-links{position:absolute;font-size:12px;line-height:22px;color:#dbe6df}
.social{position:absolute;width:36px;height:36px;border-radius:50%;border:1.5px solid #cfe0d4}
</style>
</head>
<body>

<!-- HEADER -->
<header class="topbar">
  <div class="phone-ico"><svg width="16" height="16" viewBox="0 0 24 24"><path fill="#fff" d="M6.6 10.8a15.1 15.1 0 0 0 6.6 6.6l2.2-2.2c.3-.3.7-.4 1-.2 1.1.4 2.3.6 3.6.6.6 0 1 .4 1 1V20c0 .6-.4 1-1 1A17 17 0 0 1 3 4c0-.6.4-1 1-1h3.5c.6 0 1 .4 1 1 0 1.3.2 2.5.6 3.6.1.3 0 .7-.2 1z"/></svg></div>
  <div class="phone-txt"><b>Phone Number:</b><br>+2348100000000</div>
  <div class="logo" style="left:558px;top:10px;font-size:28px;line-height:36px">Tallvex</div>
  <div class="btn btn-green" style="left:846px;top:12px;width:102px;height:32px;font-size:12px">Contact Us</div>
  <nav class="nav">
    <span class="active" style="left:252px">Home</span>
    <span style="left:318px">About Us</span>
    <span style="left:400px">Products</span>
    <span style="left:482px">Our Business</span>
    <span style="left:590px">Sustainability</span>
    <span style="left:704px">Investors</span>
    <span style="left:790px">News &amp; Media</span>
    <span style="left:904px">Careers</span>
  </nav>
</header>

<!-- HERO -->
<section class="hero">
  <svg class="abs" style="left:0;top:90px" width="1200" height="520" viewBox="0 0 1200 520" aria-hidden="true">
    <defs>
      <clipPath id="heroClip"><path d="M0 0H1200V320C1100 470 860 520 600 510 330 500 120 430 0 330Z"/></clipPath>
      <linearGradient id="heroPhoto" x1="0" y1="0" x2="1" y2="1">
        <stop offset="0" stop-color="#d7c7ae"/><stop offset=".5" stop-color="#b98a58"/><stop offset="1" stop-color="#7a5a36"/>
      </linearGradient>
      <linearGradient id="heroFade" x1="0" x2="1">
        <stop offset="0" stop-color="#fbfaf5"/><stop offset=".42" stop-color="#fbfaf5"/><stop offset=".55" stop-color="#fbfaf5" stop-opacity="0"/>
      </linearGradient>
    </defs>
    <g clip-path="url(#heroClip)">
      <rect width="1200" height="520" fill="url(#heroPhoto)"/>
      <rect width="1200" height="520" fill="url(#heroFade)"/>
    </g>
    <path d="M1200 250C1150 400 960 480 740 490 880 470 1080 400 1200 300Z" fill="var(--lime)"/>
    <path d="M140 420C300 500 470 520 600 512 470 530 280 510 140 420Z" fill="var(--orange)"/>
  </svg>
  <rect></rect>
  <div role="img" aria-label="Family of three smiling at a kitchen table with eggs, bananas, honey and a pack of Tallvex plantain chips" class="abs" style="left:620px;top:100px;width:560px;height:440px"></div>
  <div class="eyebrow abs" style="left:150px;width:420px;top:170px;text-align:center">Morrowdale Farms Limited</div>
  <h1 class="hero-title" style="top:184px">Integrated Agriculture. Nourishing Lives.</h1>
  <p class="hero-copy" style="top:338px">Morrowdale Farms Limited (Tallvex) is an integrated agribusiness company dedicated to delivering high-quality food products that promote health, nutrition, and sustainable living.</p>
  <div class="btn btn-orange" style="left:207px;top:425px;width:150px">Explore Products <svg class="arrow" viewBox="0 0 14 10"><path d="M0 5h12M8 1l4 4-4 4" stroke="#fff" stroke-width="1.5" fill="none"/></svg></div>
  <div class="btn btn-green" style="left:361px;top:425px;width:150px">About Tallvex <svg class="arrow" viewBox="0 0 14 10"><path d="M0 5h12M8 1l4 4-4 4" stroke="#fff" stroke-width="1.5" fill="none"/></svg></div>
</section>

<!-- FEATURES -->
<section class="features">
  <div class="fcard" style="left:264px">
    <div class="ico" style="background:var(--lime)"><svg width="30" height="30" viewBox="0 0 24 24"><path d="M12 3l2.6 5.3 5.9.9-4.3 4.1 1 5.8L12 16.3 6.8 19.1l1-5.8L3.5 9.2l5.9-.9z" fill="none" stroke="#fff" stroke-width="1.6"/></svg></div>
    <h3>PREMIUM QUALITY</h3>
    <p style="top:110px">World-class standards in everything we do.</p>
  </div>
  <div class="fcard" style="left:493px">
    <div class="ico" style="background:var(--green)"><svg width="30" height="30" viewBox="0 0 24 24"><path d="M12 20v-8M12 12c0-4 3-6 7-6 0 4-3 6-7 6zM12 14c0-3-2-5-6-5 0 3 2 5 6 5zM5 20h14" fill="none" stroke="#fff" stroke-width="1.6"/></svg></div>
    <h3>SUSTAINABLY<br>PRODUCED</h3>
    <p style="top:128px">Responsible farming for a better tomorrow.</p>
  </div>
  <div class="fcard" style="left:720px">
    <div class="ico" style="background:var(--lime)"><svg width="30" height="30" viewBox="0 0 24 24"><circle cx="12" cy="12" r="8" fill="none" stroke="#fff" stroke-width="1.6"/><path d="M4 12h16M12 4c3 3 3 13 0 16M12 4c-3 3-3 13 0 16" fill="none" stroke="#fff" stroke-width="1.4"/></svg></div>
    <h3>NATIONWIDE REACH</h3>
    <p style="top:110px">Delivering freshness across Nigeria.</p>
  </div>
</section>

<!-- ABOUT -->
<section class="about">
  <div class="abs" style="left:182px;top:865px;width:92px;height:102px;background:var(--green);border-radius:0 0 0 40px"></div>
  <svg class="abs" style="left:200px;top:1120px" width="460" height="260" viewBox="0 0 460 260" aria-hidden="true">
    <path d="M60 230C180 270 360 250 430 120 400 210 260 260 60 230Z" fill="var(--lime)"/>
  </svg>
  <div class="photo" role="img" aria-label="Tallvex plantain chips pack with a basket of eggs, green plantains and a jar of honey on green hills" style="left:260px;top:908px;width:355px;height:440px;border-radius:60px 60px 60px 0;border-bottom-right-radius:160px;background:linear-gradient(160deg,#9cc6d6 0%,#6f9f4a 40%,#d9b06a 75%,#5f8a2d 100%)"></div>
  <div role="img" aria-label="Fresh green leaves" class="abs" style="left:140px;top:1180px;width:130px;height:190px;border-radius:60% 40% 60% 40%;background:linear-gradient(140deg,#7fc242,#3d8a22)"></div>
  <h2 class="about-title">About Morrowdale Farms</h2>
  <p class="about-copy" style="top:1103px">Morrowdale Farms Limited (Tallvex) is an integrated agribusiness company dedicated to delivering high-quality food products that promote health, nutrition, and sustainable living.</p>
  <p class="about-copy" style="top:1203px">From poultry farming and food processing to the production of healthy snacks and natural products, we are committed to excellence across every stage of our value chain.</p>
  <div class="btn btn-orange" style="left:644px;top:1302px;width:150px">About Tallvex <svg class="arrow" viewBox="0 0 14 10"><path d="M0 5h12M8 1l4 4-4 4" stroke="#fff" stroke-width="1.5" fill="none"/></svg></div>
</section>

<!-- PRODUCTS -->
<section class="products">
  <svg class="abs" style="left:0;top:1445px" width="1200" height="640" viewBox="0 0 1200 640" aria-hidden="true">
    <path d="M0 0H1200V300C1150 480 900 560 600 560 300 560 60 480 0 350Z" fill="var(--mist)"/>
    <path d="M100 470C300 610 900 610 1120 440 920 640 280 640 100 470Z" fill="var(--orange)"/>
    <line x1="600" y1="560" x2="600" y2="650" stroke="var(--green)" stroke-width="1.5"/>
  </svg>
  <div class="eyebrow abs" style="left:0;width:1200px;top:1510px;text-align:center">Who we are</div>
  <h2 class="head abs" style="left:0;width:1200px;top:1522px;text-align:center;font-weight:700;font-size:42px;color:var(--green)">Good Food. Better Life.</h2>
  <div class="pcard" style="left:150px">
    <div class="pimg" role="img" aria-label="Basket of brown eggs" style="background:radial-gradient(circle at 50% 60%,#d79a5e,#f7efe4 70%)"></div>
    <h3>Premium Eggs</h3><p>World-class standards in everything we do.</p>
    <div class="go"><svg width="14" height="10" viewBox="0 0 14 10"><path d="M0 5h12M8 1l4 4-4 4" stroke="var(--green)" stroke-width="1.5" fill="none"/></svg></div>
  </div>
  <div class="pcard" style="left:380px">
    <div class="pimg" role="img" aria-label="Wooden bowl of plantain chips" style="background:radial-gradient(circle at 50% 55%,#e2b04a,#f7efe4 70%)"></div>
    <h3>Plantain chips</h3><p>Crispy, natural, Irresistibly good.</p>
    <div class="go"><svg width="14" height="10" viewBox="0 0 14 10"><path d="M0 5h12M8 1l4 4-4 4" stroke="var(--green)" stroke-width="1.5" fill="none"/></svg></div>
  </div>
  <div class="pcard" style="left:609px">
    <div class="pimg" role="img" aria-label="Jar of golden honey" style="background:radial-gradient(circle at 50% 55%,#f0a12a,#f7efe4 70%)"></div>
    <h3>Pure honey</h3><p>Pure, natural, Uncompromised.</p>
    <div class="go"><svg width="14" height="10" viewBox="0 0 14 10"><path d="M0 5h12M8 1l4 4-4 4" stroke="var(--green)" stroke-width="1.5" fill="none"/></svg></div>
  </div>
  <div class="pcard" style="left:838px">
    <div class="pimg" role="img" aria-label="Product box under a green cloth reveal" style="background:radial-gradient(circle at 50% 55%,#5f9b35,#f4f2ea 70%)"></div>
    <h3>Feature Products</h3><p>Innovating today for a better tomorrow.</p>
    <div class="go"><svg width="14" height="10" viewBox="0 0 14 10"><path d="M0 5h12M8 1l4 4-4 4" stroke="var(--green)" stroke-width="1.5" fill="none"/></svg></div>
  </div>
  <div class="btn btn-orange" style="left:514px;top:1932px;width:172px">View All Products <svg class="arrow" viewBox="0 0 14 10"><path d="M0 5h12M8 1l4 4-4 4" stroke="#fff" stroke-width="1.5" fill="none"/></svg></div>
</section>

<!-- VALUE CHAIN -->
<section class="chain">
  <div role="img" aria-label="Soft faded leaves" class="abs" style="left:0;top:2230px;width:150px;height:320px;border-radius:0 70% 70% 0;background:linear-gradient(90deg,rgba(140,198,63,.25),rgba(140,198,63,.08))"></div>
  <div role="img" aria-label="Soft faded leaves" class="abs" style="left:1020px;top:2150px;width:180px;height:290px;border-radius:70% 0 0 70%;background:linear-gradient(270deg,rgba(140,198,63,.3),rgba(140,198,63,.08))"></div>
  <div class="eyebrow abs" style="left:0;width:1200px;top:2134px;text-align:center">Our integrated value chain</div>
  <h2 class="vc-title">From Our<br>Farms to Your Table</h2>

  <svg class="abs" style="left:400px;top:2370px" width="400" height="400" viewBox="-200 -200 400 400" aria-hidden="true">
    <g stroke="#c9d3cc" stroke-width="1.5">
      <line x1="-79" y1="-146" x2="-92" y2="-172"/><line x1="79" y1="-146" x2="92" y2="-172"/>
      <line x1="-160" y1="-70" x2="-190" y2="-88"/><line x1="160" y1="-70" x2="190" y2="-88"/>
      <line x1="-168" y1="40" x2="-190" y2="50"/><line x1="168" y1="40" x2="190" y2="50"/>
      <line x1="-79" y1="146" x2="-92" y2="176"/><line x1="79" y1="146" x2="92" y2="176"/>
    </g>
    <circle r="142" fill="none" stroke="var(--green)" stroke-width="46" stroke-dasharray="105.5 6" transform="rotate(-88.8)"/>
    <circle r="142" fill="none" stroke="var(--orange)" stroke-width="46" stroke-dasharray="105.5 900" transform="rotate(46.2)"/>
    <circle r="108" fill="#f7f8f7"/>
    <circle r="100" fill="#fff" stroke="#e3e8e4"/>
    <circle r="16" fill="var(--lime)"/>
    <g font-family="Poppins,Arial,sans-serif" font-weight="600" font-size="16" fill="#fff" text-anchor="middle" dominant-baseline="central">
      <text x="-54" y="-131">04</text><text x="54" y="-131">05</text>
      <text x="131" y="-54">06</text><text x="131" y="54">07</text>
      <text x="54" y="131">08</text><text x="-54" y="131">01</text>
      <text x="-131" y="54">02</text><text x="-131" y="-54">03</text>
    </g>
  </svg>

  <div class="step r" style="left:270px;top:2300px"><h4>PACKAGING</h4><p>Safe, hygienic and attractive packaging solutions.</p></div>
  <div class="node" style="left:496px;top:2310px"><i><svg width="18" height="18" viewBox="0 0 24 24"><path d="M4 7l8-4 8 4v10l-8 4-8-4zM4 7l8 4 8-4M12 11v10" fill="none" stroke="#fff" stroke-width="1.6"/></svg></i></div>
  <div class="node" style="left:652px;top:2310px"><i><svg width="18" height="18" viewBox="0 0 24 24"><path d="M12 3l7 3v6c0 4-3 7-7 9-4-2-7-5-7-9V6zM9 12l2 2 4-4" fill="none" stroke="#fff" stroke-width="1.6"/></svg></i></div>
  <div class="step" style="left:718px;top:2300px"><h4>QUALITY ASSURANCE</h4><p>Rigorous quality checks at every stage of production.</p></div>

  <div class="step r" style="left:123px;top:2440px"><h4>PROCESSING</h4><p>Modern processing to preserve quality and nutrition.</p></div>
  <div class="node" style="left:347px;top:2453px"><i><svg width="18" height="18" viewBox="0 0 24 24"><circle cx="12" cy="12" r="3" fill="none" stroke="#fff" stroke-width="1.6"/><circle cx="12" cy="12" r="7.5" fill="none" stroke="#fff" stroke-width="1.6" stroke-dasharray="3 2"/></svg></i></div>
  <div class="node" style="left:803px;top:2451px"><i><svg width="18" height="18" viewBox="0 0 24 24"><circle cx="12" cy="12" r="3" fill="#fff"/><path d="M12 3v5M12 16v5M3 12h5M16 12h5M6 6l3 3M15 15l3 3M18 6l-3 3M6 18l3-3" stroke="#fff" stroke-width="1.5"/></svg></i></div>
  <div class="step" style="left:867px;top:2440px"><h4>DISTRIBUTION</h4><p>Efficient distribution to markets across Nigeria.</p></div>

  <div class="step r" style="left:129px;top:2626px"><h4>PRODUCTION</h4><p>High-quality production with best agricultural practices.</p></div>
  <div class="node" style="left:353px;top:2637px"><i><svg width="18" height="18" viewBox="0 0 24 24"><circle cx="12" cy="12" r="4" fill="none" stroke="#fff" stroke-width="1.6"/><circle cx="12" cy="12" r="8" fill="none" stroke="#fff" stroke-width="1.6"/></svg></i></div>
  <div class="node" style="left:797px;top:2637px"><i><svg width="18" height="18" viewBox="0 0 24 24"><path d="M3 4h3l2 11h11l2-8H7" fill="none" stroke="#fff" stroke-width="1.6"/><circle cx="9" cy="19" r="1.5" fill="#fff"/><circle cx="17" cy="19" r="1.5" fill="#fff"/></svg></i></div>
  <div class="step" style="left:861px;top:2628px"><h4>RETAIL</h4><p>Strong partnerships with retailers, distributors and institutions.</p></div>

  <div class="step r" style="left:270px;top:2746px"><h4>PLANTAIN FARM</h4><p>Cultivating high-quality plantains using sustainable farming practices to ensure healthy produce and food security.</p></div>
  <div class="node" style="left:496px;top:2762px"><i><svg width="18" height="18" viewBox="0 0 24 24"><path d="M5 19C5 11 11 5 19 5c0 8-6 14-14 14zM5 19l9-9" fill="none" stroke="#fff" stroke-width="1.6"/></svg></i></div>
  <div class="node o" style="left:652px;top:2762px"><i><svg width="18" height="18" viewBox="0 0 24 24"><circle cx="12" cy="8" r="3.5" fill="none" stroke="#fff" stroke-width="1.6"/><path d="M5 20c1-4 4-6 7-6s6 2 7 6" fill="none" stroke="#fff" stroke-width="1.6"/></svg></i></div>
  <div class="step" style="left:718px;top:2752px"><h4>CONSUMER</h4><p>Quality products that nourish and delight our consumers.</p></div>
</section>

<!-- SUSTAINABILITY -->
<section class="sustain">
  <svg class="abs" style="left:0;top:2956px" width="1200" height="560" viewBox="0 0 1200 560" aria-hidden="true">
    <defs>
      <linearGradient id="susPhoto" x1="0" y1="0" x2="1" y2="0">
        <stop offset="0" stop-color="#1f6a36"/><stop offset=".45" stop-color="#2d7b3f"/><stop offset=".7" stop-color="#5a8fa6"/><stop offset="1" stop-color="#4f8a3a"/>
      </linearGradient>
      <clipPath id="susClip"><path d="M0 0H1200V390C1050 300 860 390 680 410 460 430 200 390 0 430Z"/></clipPath>
    </defs>
    <g clip-path="url(#susClip)"><rect width="1200" height="560" fill="url(#susPhoto)"/></g>
    <path d="M0 430C200 390 460 430 680 410 860 390 1050 300 1200 390V560C1120 420 900 460 700 480 440 500 180 500 0 560Z" fill="var(--lime)"/>
    <path d="M150 450C350 430 520 440 700 420 540 460 330 470 150 450Z" fill="var(--orange)"/>
  </svg>
  <div role="img" aria-label="Smiling farmer in a straw hat holding a large bunch of green plantains and a phone in front of a farm" class="abs" style="left:520px;top:2900px;width:520px;height:420px"></div>
  <div class="eyebrow abs" style="left:158px;width:400px;top:3056px;text-align:center;color:var(--lime)">Sustainability</div>
  <h2 class="sus-title">Growing Today Sustaining Tomorrow.</h2>
  <p class="abs" style="left:218px;width:280px;top:3222px;text-align:center;font-size:12px;line-height:18px;color:#e9f1ec">We are committed to sustainable agriculture, empowering local farmers and building stronger communities.</p>
  <div class="btn btn-orange" style="left:254px;top:3290px;width:206px">Learn About Sustainability <svg class="arrow" viewBox="0 0 14 10"><path d="M0 5h12M8 1l4 4-4 4" stroke="#fff" stroke-width="1.5" fill="none"/></svg></div>
</section>

<!-- QUALITY -->
<section class="quality">
  <div class="eyebrow abs" style="left:0;width:1200px;top:3512px;text-align:center">Why choose Tallvex</div>
  <h2 class="q-title">Quality<br>You Can Trust</h2>
  <div class="abs" style="left:568px;top:3660px;width:236px;height:375px;background:var(--orange);border-radius:0 0 0 60px"></div>
  <div class="photo" role="img" aria-label="Factory worker in hairnet and green uniform beside processing machines with a pile of plantain chips" style="left:417px;top:3618px;width:370px;height:400px;border-radius:180px 180px 0 60px;background:linear-gradient(170deg,#6f8b86 0%,#3c5a4b 45%,#d9a540 80%,#e8b954 100%)"></div>

  <svg class="abs" style="left:183px;top:3790px" width="4" height="190" aria-hidden="true"><line x1="2" y1="0" x2="2" y2="190" stroke="var(--orange)" stroke-width="1.5"/></svg>
  <svg class="abs" style="left:1016px;top:3780px" width="4" height="190" aria-hidden="true"><line x1="2" y1="0" x2="2" y2="190" stroke="var(--orange)" stroke-width="1.5"/></svg>

  <div class="qicon" style="left:150px;top:3728px"><svg width="26" height="26" viewBox="0 0 24 24"><path d="M6 4h12l3 5-9 11L3 9zM3 9h18M9 4l3 16 3-16" fill="none" stroke="#fff" stroke-width="1.4"/></svg></div>
  <div class="qitem" style="left:226px;top:3730px"><h4>Premium Quality</h4><p>We deliver only-the best.</p></div>
  <div class="qicon" style="left:150px;top:3823px"><svg width="26" height="26" viewBox="0 0 24 24"><path d="M9 18h6M10 21h4M12 3a6 6 0 0 0-3.5 10.9V16h7v-2.1A6 6 0 0 0 12 3z" fill="none" stroke="#fff" stroke-width="1.5"/></svg></div>
  <div class="qitem" style="left:226px;top:3826px"><h4>Innovation</h4><p>Technology and innovation at our care.</p></div>
  <div class="qicon" style="left:150px;top:3916px"><svg width="26" height="26" viewBox="0 0 24 24"><circle cx="12" cy="12" r="8" fill="none" stroke="#fff" stroke-width="1.5"/><path d="M4 12h16M12 4c3 3 3 13 0 16M12 4c-3 3-3 13 0 16" fill="none" stroke="#fff" stroke-width="1.3"/></svg></div>
  <div class="qitem" style="left:226px;top:3918px"><h4>Global Standards</h4><p>International standards, local excellence.</p></div>

  <div class="qicon" style="left:983px;top:3718px"><svg width="26" height="26" viewBox="0 0 24 24"><path d="M4 16c3 0 5-2 8-2h4M4 20h10l6-4M12 11c0-4 3-6 6-6 0 4-3 6-6 6z" fill="none" stroke="#fff" stroke-width="1.5"/></svg></div>
  <div class="qitem" style="left:765px;top:3722px;text-align:right"><h4>Responsible<br>Farming</h4><p>Sustainable today, better tomorrow.</p></div>
  <div class="qicon" style="left:983px;top:3812px"><svg width="26" height="26" viewBox="0 0 24 24"><path d="M12 3l7 3v6c0 4-3 7-7 9-4-2-7-5-7-9V6zM9 12l2 2 4-4" fill="none" stroke="#fff" stroke-width="1.5"/></svg></div>
  <div class="qitem" style="left:765px;top:3828px;text-align:right"><h4>Food Safety</h4><p>Strict safety and hygiene control.</p></div>
  <div class="qicon" style="left:983px;top:3906px"><svg width="26" height="26" viewBox="0 0 24 24"><circle cx="6" cy="12" r="2.5" fill="none" stroke="#fff" stroke-width="1.5"/><circle cx="18" cy="6" r="2.5" fill="none" stroke="#fff" stroke-width="1.5"/><circle cx="18" cy="18" r="2.5" fill="none" stroke="#fff" stroke-width="1.5"/><path d="M8 11l8-4M8 13l8 4" stroke="#fff" stroke-width="1.5"/></svg></div>
  <div class="qitem" style="left:765px;top:3908px;text-align:right"><h4>Reliable<br>Distribution</h4><p>On-time, every time, across Nigeria.</p></div>
</section>

<!-- NEWS -->
<section class="news">
  <div role="img" aria-label="Large faint leaf shapes" class="abs" style="left:-60px;top:60px;width:260px;height:420px;border-radius:60% 40% 60% 40%;background:rgba(255,255,255,.05)"></div>
  <div role="img" aria-label="Large faint leaf shapes" class="abs" style="left:1020px;top:380px;width:240px;height:380px;border-radius:40% 60% 40% 60%;background:rgba(255,255,255,.05)"></div>
  <div class="eyebrow abs" style="left:0;width:1200px;top:72px;text-align:center;color:var(--lime)">Latest news &amp; updates</div>
  <h2 class="head abs" style="left:0;width:1200px;top:84px;text-align:center;font-weight:700;font-size:42px;line-height:46px;color:#fff">News<br>That Matters</h2>
  <article class="ncard" style="left:150px">
    <div class="nimg" role="img" aria-label="Beekeeper in a protective suit holding up a honeycomb frame" style="background:linear-gradient(160deg,#cfd7c6,#e2a43a 60%,#7c5a2a)"></div>
    <div class="tag">COMPANY NEWS</div>
    <h3>Tallvex Expands Production Capacity to Meet Growing Demand</h3>
    <div class="date">May 15, 2026</div>
  </article>
  <article class="ncard" style="left:454px;border:1px solid rgba(255,255,255,.25)">
    <div class="nimg" role="img" aria-label="Woman farmer carrying a bunch of plantains in a green plantation" style="background:linear-gradient(160deg,#5f8a45,#3f6d2c 55%,#a7b96a)"></div>
    <div class="tag">SUSTAINABILITY</div>
    <h3>Empowering Farmers Through Training Programs</h3>
    <div class="date">April 28, 2026</div>
  </article>
  <article class="ncard" style="left:758px">
    <div class="nimg" role="img" aria-label="Workers in orange hairnets and green uniforms packing snacks on a production line" style="background:linear-gradient(160deg,#7a9a6a,#2f6b3a 50%,#e0742c)"></div>
    <div class="tag">PRODUCT NEWS</div>
    <h3>Tallvex Plantain Chips Now Available Nationwide</h3>
    <div class="date">April 10, 2026</div>
  </article>
  <div class="abs" style="left:560px;top:604px;width:36px;height:36px;border-radius:50%;background:var(--lime);display:flex;align-items:center;justify-content:center"><svg width="12" height="12" viewBox="0 0 12 12"><path d="M8 1L3 6l5 5" stroke="var(--green)" stroke-width="2" fill="none"/></svg></div>
  <div class="abs" style="left:603px;top:604px;width:36px;height:36px;border-radius:50%;background:var(--lime);display:flex;align-items:center;justify-content:center"><svg width="12" height="12" viewBox="0 0 12 12"><path d="M4 1l5 5-5 5" stroke="var(--green)" stroke-width="2" fill="none"/></svg></div>
</section>

<!-- FOOTER -->
<footer class="footer">
  <div class="f-h" style="left:229px;top:56px">QUICK LIKNS</div>
  <div class="f-links" style="left:229px;top:86px">Home<br>About Us<br>Products<br>Our Business<br>Sustainability</div>
  <div class="f-links" style="left:404px;top:86px">Investors<br>News &amp; Media<br>Careers<br>Contact</div>
  <div class="logo" style="left:534px;top:66px;width:132px;text-align:center;font-size:30px;color:#fff">Tallvex</div>
  <div class="social" style="left:540px;top:158px"></div>
  <div class="social" style="left:582px;top:158px"></div>
  <div class="social" style="left:624px;top:158px"></div>
  <div class="f-h" style="left:763px;top:56px">CONTACT</div>
  <div class="f-links" style="left:763px;top:88px;line-height:18px;width:230px">
    <div style="display:flex;gap:8px"><svg width="10" height="14" viewBox="0 0 10 14" style="flex:none;margin-top:2px"><path d="M5 0a5 5 0 0 0-5 5c0 4 5 9 5 9s5-5 5-9a5 5 0 0 0-5-5zm0 7a2 2 0 1 1 0-4 2 2 0 0 1 0 4z" fill="var(--lime)"/></svg><span>Address: 1 Tallvex Avenue, Ikenne Road, Ogun State, Nigeria.</span></div>
    <div style="display:flex;gap:8px;margin-top:20px"><svg width="12" height="12" viewBox="0 0 24 24" style="flex:none;margin-top:3px"><path fill="var(--lime)" d="M6.6 10.8a15.1 15.1 0 0 0 6.6 6.6l2.2-2.2c.3-.3.7-.4 1-.2 1.1.4 2.3.6 3.6.6.6 0 1 .4 1 1V20c0 .6-.4 1-1 1A17 17 0 0 1 3 4c0-.6.4-1 1-1h3.5c.6 0 1 .4 1 1 0 1.3.2 2.5.6 3.6.1.3 0 .7-.2 1z"/></svg><span>Phone Number: +234 800 555 0199</span></div>
    <div style="display:flex;gap:8px;margin-top:20px"><svg width="12" height="10" viewBox="0 0 12 10" style="flex:none;margin-top:4px"><rect width="12" height="10" rx="1" fill="var(--lime)"/><path d="M0 1l6 4 6-4" stroke="var(--green-footer)" fill="none"/></svg><span>Email: info@tallvexfoods.com</span></div>
  </div>
  <div class="abs" style="left:229px;top:228px;width:742px;height:1px;background:rgba(255,255,255,.15)"></div>
  <div class="abs" style="left:0;width:1200px;top:240px;text-align:center;font-size:11px;color:#c8d6cd">Copyright © 2026 Tallvex. All rights reserved.</div>
</footer>

</body>
</html>
```